Melorix artwork for new single release

I need Melorix artwork creating to release a new single on there.

The specs are:

Ideal size: 3000 x 3000 pixels
Minimum size: 1400 x 1400 pixels
Aspect ratio: 1:1 (must be a perfect square)
File format: JPG or PNG
Color space: sRGB
File size: Max 4MB

The song is called "Was It Ever Rain?"
The artist is "Martin Hollow"

We have no images of Martin, so it really is open to imagination.

Target Market(s)

Melorix listeners

Industry/Entity Type

Music

```html
<!DOCTYPE html>
<html lang="en">
<head>
<meta charset="utf-8">
<title>Now Playing – Was It Ever Rain?</title>
<link href="https://fonts.googleapis.com/css2?family=Plus+Jakarta+Sans:wght@400;500;700&family=Libre+Baskerville:wght@400;700&display=swap" rel="stylesheet">
<style>
  :root {
    --bg: #232323;
    --text: #ffffff;
    --muted: #c9c9c9;
    --track: #cfcfcf;
    --accent: #1ec85a;
    --art-bg: #163246;
    --art-text: #dfe8ee;
    --heart-a: #8ee9d6;
    --heart-b: #3fd6c9;
    --heart-c: #1f7fe0;
  }
  * { margin: 0; padding: 0; box-sizing: border-box; }
  html, body { width: 675px; height: 1200px; overflow: hidden; background: var(--bg); }
  body { font-family: "Plus Jakarta Sans", sans-serif; color: var(--text); position: relative; }

  .header { position: absolute; top: 0; left: 0; width: 675px; height: 130px; }
  .header .collapse { position: absolute; left: 56px; top: 62px; }
  .header .more { position: absolute; left: 611px; top: 51px; }
  .header .source { position: absolute; top: 61px; width: 100%; text-align: center; font-size: 17.5px; font-weight: 500; letter-spacing: 0.3px; }
  .header .playlist { position: absolute; top: 91px; width: 100%; text-align: center; font-size: 19.5px; font-weight: 700; }

  .cover { position: absolute; left: 47px; top: 164px; width: 581px; height: 581px; border-radius: 17px; background: var(--art-bg); overflow: hidden; }
  .cover-artist { position: absolute; left: 0; top: 46px; width: 100%; text-align: center; font-family: "Libre Baskerville", serif; font-size: 33px; line-height: 40px; letter-spacing: 9px; padding-left: 9px; color: var(--art-text); z-index: 1; }
  .cover-art { position: absolute; left: 122px; top: 127px; width: 340px; height: 340px; border-radius: 45% 45% 50% 50%; background: radial-gradient(circle at 55% 45%, var(--heart-b), var(--heart-a) 45%, var(--heart-c) 100%); opacity: 0.85; }
  .cover-title { position: absolute; left: 0; top: 488px; width: 100%; text-align: center; font-family: "Libre Baskerville", serif; font-weight: 700; font-size: 36px; line-height: 44px; color: var(--art-text); z-index: 1; }

  .track-title { position: absolute; left: 46px; top: 786px; font-size: 40px; font-weight: 700; letter-spacing: -0.5px; }
  .track-artist { position: absolute; left: 50px; top: 844px; font-size: 20px; color: var(--muted); }

  .progress { position: absolute; left: 54px; top: 902px; width: 564px; height: 2px; background: var(--track); border-radius: 1px; }
  .progress .knob { position: absolute; left: -7px; top: -6px; width: 14px; height: 14px; border-radius: 50%; background: var(--text); }
  .time { position: absolute; top: 923px; font-size: 19px; color: var(--muted); }
  .time.elapsed { left: 49px; }
  .time.total { right: 55px; }

  .controls svg, .footer svg { position: absolute; }
  .play { position: absolute; left: 291px; top: 980px; width: 98px; height: 98px; border-radius: 50%; background: var(--text); }
</style>
</head>
<body>
  <header class="header">
    <svg class="collapse" width="22" height="14" viewBox="0 0 22 14"><path d="M1 2 L11 11 L21 2" fill="none" stroke="var(--text)" stroke-width="2"/></svg>
    <div class="source">PLAYING FROM YOUR LIBRARY</div>
    <div class="playlist">Love Playlist</div>
    <svg class="more" width="12" height="34" viewBox="0 0 12 34"><circle cx="6" cy="4" r="3.3" fill="var(--text)"/><circle cx="6" cy="17" r="3.3" fill="var(--text)"/><circle cx="6" cy="30" r="3.3" fill="var(--text)"/></svg>
  </header>

  <section class="cover">
    <div class="cover-artist">MARTIN HOLLOW</div>
    <div class="cover-art" role="img" aria-label="Heart shaped fingerprint illustration in teal and blue on a starry night sky"></div>
    <div class="cover-title">Was It Ever Rain?</div>
  </section>

  <h1 class="track-title">Was It Ever Rain?</h1>
  <p class="track-artist">Martin Hollow</p>

  <div class="progress"><span class="knob"></span></div>
  <span class="time elapsed">0:00</span>
  <span class="time total">03:18</span>

  <div class="controls">
    <svg style="left:50px;top:1010px" width="40" height="42" viewBox="0 0 40 42">
      <g fill="none" stroke="var(--accent)" stroke-width="2.6">
        <path d="M3 9 H11 C18 9 20 25 28 25 H36"/>
        <path d="M3 25 H11 C14 25 16 21 17 18"/>
        <path d="M22 13 C24 10 25 9 28 9 H36"/>
        <path d="M31 4 L36 9 L31 14"/><path d="M31 20 L36 25 L31 30"/>
      </g>
      <circle cx="18" cy="38" r="2" fill="var(--accent)"/>
    </svg>
    <svg style="left:186px;top:1010px" width="36" height="38" viewBox="0 0 36 38"><rect x="0" y="0" width="6" height="38" fill="var(--text)"/><path d="M35 0 V38 L6 19 Z" fill="var(--text)"/></svg>
    <div class="play"></div>
    <svg style="left:328px;top:1013px" width="30" height="32" viewBox="0 0 30 32"><path d="M2 0 V32 L28 16 Z" fill="#111"/></svg>
    <svg style="left:456px;top:1010px" width="36" height="38" viewBox="0 0 36 38"><path d="M1 0 V38 L30 19 Z" fill="var(--text)"/><rect x="30" y="0" width="6" height="38" fill="var(--text)"/></svg>
    <svg style="left:581px;top:1011px" width="42" height="42" viewBox="0 0 42 42">
      <g fill="none" stroke="var(--accent)" stroke-width="2.6">
        <path d="M20 26 H6 Q3 26 3 23 V6 Q3 3 6 3 H36 Q39 3 39 6 V23 Q39 26 36 26 H28"/>
        <path d="M23 21 L18 26 L23 31"/>
      </g>
      <circle cx="21" cy="39" r="2" fill="var(--accent)"/>
    </svg>
  </div>

  <footer class="footer">
    <svg style="left:51px;top:1103px" width="34" height="32" viewBox="0 0 34 32">
      <g fill="none" stroke="var(--text)" stroke-width="2.4">
        <path d="M11 2 H3 V28 H8"/>
        <rect x="16" y="2" width="16" height="28" rx="3"/>
        <circle cx="24" cy="19" r="4"/>
      </g>
      <circle cx="24" cy="8" r="1.8" fill="var(--text)"/>
      <circle cx="10" cy="29" r="1.8" fill="var(--text)"/>
    </svg>
    <svg style="left:524px;top:1107px" width="26" height="26" viewBox="0 0 26 26">
      <g fill="none" stroke="var(--text)" stroke-width="2.2">
        <circle cx="20" cy="5" r="3.5"/><circle cx="5" cy="13" r="3.5"/><circle cx="20" cy="21" r="3.5"/>
        <path d="M8 11 L17 6.5 M8 15 L17 19.5"/>
      </g>
    </svg>
    <svg style="left:599px;top:1108px" width="25" height="22" viewBox="0 0 25 22">
      <g fill="none" stroke="var(--text)" stroke-width="2.2">
        <rect x="1" y="1" width="23" height="6" rx="1"/>
        <path d="M1 13 H24 M1 20 H24"/>
      </g>
    </svg>
  </footer>
</body>
</html>
```